real esate business card with company logo and name

we need a business card design for a real esate company

The company name is Walsh & Brand Pty Ltd, and we have our logo designed and will upload. We want classic or moden feel. Black or white background. looks more textured. Should include folowinginformations
Owen Walsh and Lucy Brand
Sales Agents & Onsite Manager
p: 07 5948 2063
F: 07 5948 2174
M:0431 857 219
3/42 Marlow Crescent, FERNLEA QLD 4213

We want this business card looks professonal. Thank you in advance.

Industry/Entity Type

Real Estate Agent

Contact Information for Business Card

Owen Walsh and Lucy Brand
Onsite Manager & Sales Agents
p: 07 5948 2063
M:0431 857 219

Font styles to use
Serif

Colors
000000
fbfbfb
333333
959595

Requirements
Must have
• company logo and name, black or white back ground

```html
<!DOCTYPE html>
<html lang="en">
<head>
<meta charset="utf-8">
<title>Walsh &amp; Brand Pty Ltd — Business Card</title>
<link rel="stylesheet" href="https://fonts.googleapis.com/css2?family=Cinzel:wght@400;500&display=swap">
<style>
  :root {
    --ink: #000000;
    --paper: #fbfbfb;
    --charcoal: #333333;
    --silver: #959595;
    --silver-light: #c9c9c9;
    --silver-pale: #e2e2e2;
    --backdrop: #e9e7e4;
  }
  * { box-sizing: border-box; margin: 0; padding: 0; }
  html, body {
    width: 1200px;
    height: 913px;
    overflow: hidden;
    background: var(--backdrop);
    font-family: "Cinzel", "Times New Roman", serif;
  }
  .canvas {
    position: relative;
    width: 1200px;
    height: 913px;
  }
  .card {
    position: absolute;
    width: 600px;
    height: 343px;
    border-radius: 4px;
    box-shadow: 0 10px 28px rgba(0,0,0,0.18), 0 2px 6px rgba(0,0,0,0.12);
    overflow: hidden;
  }
  .card--front {
    left: 80px;
    top: 90px;
    background: var(--paper);
  }
  .card--back {
    left: 520px;
    top: 480px;
    background: linear-gradient(135deg, #0b0b0b 0%, var(--ink) 45%, #1a1a1a 70%, var(--ink) 100%);
  }
  .brand {
    position: absolute;
    left: 0;
    right: 0;
    display: flex;
    flex-direction: column;
    align-items: center;
  }
  .brand__mark {
    width: 46px;
    height: 46px;
    background: var(--silver);
  }
  .brand__name {
    margin-top: 12px;
    font-weight: 400;
    letter-spacing: 0.14em;
    text-transform: uppercase;
    color: var(--silver);
    white-space: nowrap;
  }
  .card--front .brand { top: 38px; }
  .card--front .brand__name { font-size: 13px; }
  .card--back .brand { top: 112px; }
  .card--back .brand__mark { width: 64px; height: 64px; background: var(--silver-light); }
  .card--back .brand__name { margin-top: 24px; font-size: 19px; color: #8a8a8a; }

  .people {
    position: absolute;
    top: 156px;
    left: 0;
    right: 0;
    text-align: center;
  }
  .people__names {
    font-size: 24px;
    font-weight: 400;
    color: var(--ink);
    letter-spacing: 0.02em;
  }
  .people__role {
    margin-top: 4px;
    font-size: 12px;
    color: var(--silver);
    letter-spacing: 0.08em;
  }
  .contact-band {
    position: absolute;
    left: 0;
    right: 0;
    top: 232px;
    height: 74px;
    background: linear-gradient(180deg, var(--silver-pale) 0%, var(--silver-light) 40%, var(--silver) 75%, var(--silver-light) 100%);
    display: flex;
    flex-direction: column;
    justify-content: center;
    align-items: center;
    gap: 6px;
    color: var(--charcoal);
  }
  .contact-band__line {
    font-size: 13px;
    letter-spacing: 0.03em;
    white-space: nowrap;
  }
  .contact-band__line b { font-weight: 500; color: var(--ink); }
</style>
</head>
<body>
<main class="canvas">

  <section class="card card--front" aria-label="Business card front">
    <div class="brand">
      <span class="brand__mark" aria-hidden="true"></span>
      <span class="brand__name">Walsh &amp; Brand Pty Ltd.</span>
    </div>

    <div class="people">
      <h1 class="people__names">Owen Walsh &amp; Lucy Brand</h1>
      <p class="people__role">Sales Agents &amp; Onsite Manager</p>
    </div>

    <div class="contact-band">
      <p class="contact-band__line"><b>P</b> 07 5948 2063 &nbsp;·&nbsp; <b>F</b> 07 5948 2174 &nbsp;·&nbsp; <b>M</b> 0431 857 219</p>
      <p class="contact-band__line"><b>A</b> 3/42 Marlow Crescent, FERNLEA QLD 4213</p>
    </div>
  </section>

  <section class="card card--back" aria-label="Business card back">
    <div class="brand">
      <span class="brand__mark" aria-hidden="true"></span>
      <span class="brand__name">Walsh &amp; Brand Pty Ltd.</span>
    </div>
  </section>

</main>
</body>
</html>
```